IV Nutritional Clinic Web Design

We are working with Velqo. They are an IV Nutritional Clinic and in need of a new website design.
Some sites to use for inspiration:
https://brightpathcareco.com
https://www.ourzavrowellness.com
https://www.dewspringlounge.com
https://qvitalsurge.com
https://www.lumo-vital.com/pages/iv-therapy-west-hollywood
https://www.tqoncologyhub.com/cancer-care/iv-drips/
https://dripwellary.com
https://corvinahealthhub.com
Thank you for taking the time to consider designing a website for us. We are web developers based in Stockton, CA, USA. Most of our projects go through the same process. Understanding this process may help you win a project with us. We custom-code all of our websites in-house. We don’t have any requirements as to what tools you use for your design, but we prefer Figma files. For any design that we label as four-stars, we send it to the client for review. The client picks the final design they want us to use. Once we complete this process, we will continue to show additional clients all the four-star sites and purchase them later. Your designs will have multiple chances to sell. For better chances of success, we ask that you follow these guidelines.
IMAGES:
If you use any images or icons in the design, we ask that you have a link to the asset so we can purchase the image/icon. Most of the designs we submit do not have the customer’s images on them unless they have some great images. Be creative; show us the feeling you are trying to portray with your image choices. Use any royalty-free site you choose. We subscribe to Pixvane and mainly use their images, but we can purchase images outside of Pixvane.
PLEASE NOTE: we will not submit designs to clients with watermarks on the images.
FONTS:
We ask that you identify the fonts used in the design. This can be done in a message if you want. We typically use Google Fonts and Pixvane Fonts.
CONTENT:
We're always open to different content and ideas. We often submit designs with stock images so the client can see our vision. We typically take pictures after the website launch to use their images with our vision. Lorem Ipsum is fine for paragraphs, but we ask that you write the headers in correct English. We want to be able to show the vision and identify the sections of the website.
INSPIRATION:
We typically add a couple of links in the brief of websites we like to help you get started in your design.
REVISIONS:
We do not often ask for revisions of the designs unless we see something in the design that may not appeal to the client. If there are slight changes that we want to make, we do that in the development process.
FEEDBACK:
We rarely give feedback on designs during the design process. We are working on many website projects and do not have the time to provide feedback. We usually respond if your request is well thought out and asks specific questions, but a note asking “feedback, please” usually goes unanswered.

```html
<!DOCTYPE html>
<html lang="en">
<head>
<meta charset="utf-8">
<title>Velqo – IV Nutritional Therapy</title>
<link href="https://fonts.googleapis.com/css2?family=Outfit:wght@400;500;600;700;900&family=Poppins:wght@400;500;600&display=swap" rel="stylesheet">
<style>
:root{
  --navy:#221d8f;
  --navy-deep:#1a1678;
  --green:#6b9b2e;
  --lavender:#f3f2fd;
  --card:#eeedfb;
  --ink:#2a2a3a;
  --muted:#55566a;
  --white:#ffffff;
  --black:#0b0b0d;
}
*{margin:0;padding:0;box-sizing:border-box}
html,body{width:1200px;height:4894px;overflow:hidden}
body{font-family:"Poppins",sans-serif;color:var(--ink);background:var(--white)}
h1,h2,h3,h4{font-family:"Outfit",sans-serif;color:var(--navy);font-weight:600}
section,header,footer{position:relative;width:1200px;overflow:hidden}
.btn{display:inline-block;background:var(--green);color:var(--white);font-family:"Outfit",sans-serif;font-weight:700;font-size:12px;letter-spacing:.6px;text-transform:uppercase;border-radius:22px;text-align:center;text-decoration:none}
.rule{width:46px;height:2px;background:var(--navy)}

/* brand */
.brand{position:absolute;font-family:"Outfit",sans-serif;font-weight:700;color:var(--navy);line-height:1;letter-spacing:1px}
.hero .brand{left:161px;top:26px;font-size:38px}

/* hero */
.hero{height:593px;background:linear-gradient(100deg,#f4f5f8 0%,#e9ecf1 40%,#d9dfe8 70%,#eef0f4 100%)}
.hero-photo{position:absolute;inset:0;background:radial-gradient(ellipse 160px 260px at 700px 330px,#a9c0e0 0%,rgba(169,192,224,0) 100%),radial-gradient(ellipse 120px 110px at 670px 130px,#b78f76 0%,rgba(183,143,118,0) 100%),linear-gradient(90deg,rgba(255,255,255,0) 0%,rgba(214,222,232,.6) 100%)}
.nav{position:absolute;left:400px;top:29px;display:flex;align-items:center;font-size:11px;text-transform:uppercase;color:var(--ink)}
.nav a{color:var(--ink);text-decoration:none;padding:6px 11px}
.nav a.active{background:var(--green);color:var(--white);border-radius:14px;padding:6px 12px;margin-right:6px}
.nav a.book{background:var(--navy);color:var(--white);border-radius:16px;padding:8px 20px;margin-left:14px}
.hero h1{position:absolute;left:156px;top:222px;font-size:52px;line-height:1.1;font-weight:600}
.hero h1 .accent{color:var(--green)}
.hero p{position:absolute;left:156px;top:356px;font-size:16.5px;line-height:1.55;width:380px;color:var(--ink)}
.hero .btn{position:absolute;left:156px;top:431px;width:229px;height:38px;line-height:38px;font-size:13px}

/* benefits */
.benefits{height:600px}
.benefits .photo{position:absolute;left:165px;top:58px;width:410px;height:477px;background:linear-gradient(160deg,#cfe3f2 0%,#b7d2ea 40%,#8fb6da 100%)}
.benefits h2{position:absolute;left:625px;top:50px;font-size:38px;line-height:1.2}
.benefits .rule{position:absolute;left:625px;top:158px}
.benefits .intro{position:absolute;left:625px;top:184px;width:410px;font-size:11px;line-height:1.6;color:var(--muted)}
.benefit{position:absolute;left:627px;width:400px;display:flex;gap:18px}
.benefit .ico{width:45px;height:45px;border-radius:50%;background:var(--navy);flex:none;display:flex;align-items:center;justify-content:center}
.benefit h4{font-size:12px;font-weight:600;margin-bottom:3px}
.benefit p{font-size:10px;line-height:1.5;color:var(--muted);width:310px}

/* featured */
.featured{height:1437px;background:var(--lavender)}
.featured h2,.live h2,.testimonials h2{position:absolute;left:0;width:1200px;text-align:center;font-size:38px}
.featured h2{top:48px}
.featured .rule{position:absolute;left:577px;top:118px}
.therapy-text{position:absolute;width:260px}
.therapy-text h3{font-size:30px;line-height:1.2;margin-bottom:22px}
.therapy-text p{font-size:10.5px;line-height:1.62;color:var(--muted);margin-bottom:22px}
.therapy-text .btn{width:178px;height:30px;line-height:30px;font-size:10px}
.therapy-photo{position:absolute;width:555px;height:376px}

/* testimonials */
.testimonials{height:589px;background:radial-gradient(ellipse at 30% 40%,#2a25a0 0%,var(--navy-deep) 70%)}
.testimonials h2{top:46px;color:var(--white)}
.testimonials .rule{position:absolute;left:577px;top:118px;background:var(--white)}
.t-card{position:absolute;left:163px;top:163px;width:872px;height:334px;background:var(--white);display:flex}
.t-photo{width:370px;height:334px;background:linear-gradient(180deg,#f3b24a 0%,#e78b1e 45%,#a3521a 80%,#5b3215 100%)}
.t-body{padding:34px 70px 0 40px;width:502px}
.t-mark{font-family:"Outfit",sans-serif;font-size:56px;color:var(--navy);line-height:.7;height:34px}
.t-body p{font-size:13px;line-height:1.62;color:var(--muted);margin-top:4px}
.t-rule{width:40px;height:1.5px;background:var(--navy);margin:28px 0 12px}
.t-name{font-family:"Outfit",sans-serif;font-size:13px;color:var(--navy);font-weight:600}
.dots{position:absolute;top:534px;left:0;width:1200px;display:flex;justify-content:center;gap:14px}
.dots span{width:8px;height:8px;border-radius:50%;background:var(--white)}
.dots span.on{background:var(--green)}

/* live */
.live{height:513px}
.live h2{top:52px}
.live .rule{position:absolute;left:577px;top:127px}
.drip{position:absolute;left:44px;top:0;width:120px;height:410px;background:linear-gradient(180deg,#dfe6ee 0%,#c5cfd9 30%,rgba(210,218,226,.4) 70%,rgba(255,255,255,0) 100%)}
.live-card{position:absolute;top:190px;width:277px;height:272px;background:var(--card);text-align:center;padding-top:40px}
.live-card svg{display:block;margin:0 auto 20px}
.live-card h3{font-size:18px;font-weight:600;margin-bottom:12px}
.live-card p{font-size:10px;line-height:1.55;color:var(--muted);padding:0 34px}

/* treatments */
.treat{height:446px}
.treat h2{position:absolute;left:165px;top:52px;font-size:40px;line-height:1.12;font-weight:900;letter-spacing:-1.6px}
.treat .rule{position:absolute;left:165px;top:210px}
.treat p{position:absolute;left:165px;top:238px;width:262px;font-size:10px;line-height:1.6;color:var(--muted)}
.treat .btn{position:absolute;left:165px;top:368px;width:110px;height:30px;line-height:30px;font-size:10px}
.treat .photo{position:absolute;left:507px;top:53px;width:528px;height:357px;background:linear-gradient(120deg,#e6e9ee 0%,#d3d9e0 50%,#b9a495 70%,#e8ebee 100%)}

/* schedule */
.schedule{height:418px;background:radial-gradient(ellipse 500px 250px at 620px 180px,#3d3ab4 0%,rgba(34,29,143,0) 100%),linear-gradient(180deg,#2a26a2 0%,var(--navy-deep) 100%);text-align:center;color:var(--white)}
.schedule h2{color:var(--white);font-size:40px;padding-top:72px;font-weight:600}
.schedule .sub{font-size:17px;margin-top:8px;color:#e6e6f6}
.schedule .body{font-size:17.5px;line-height:1.7;width:780px;margin:42px auto 0;color:#e6e6f6}
.schedule .btn{margin-top:42px;width:224px;height:38px;line-height:38px;font-size:12.5px}

/* footer */
.site-footer{height:298px;background:var(--black);color:var(--white)}
.site-footer .brand{left:161px;top:64px;font-size:56px}
.f-col{position:absolute;top:57px}
.f-col h4{color:var(--white);font-size:11px;font-weight:600;font-family:"Poppins",sans-serif;margin-bottom:14px}
.f-col li{list-style:none;font-size:9px;line-height:1.55;display:flex;gap:10px;margin-bottom:18px;color:#e8e8ee}
.f-menu li{margin-bottom:0;line-height:1.6}
.socials{display:flex;gap:5px}
.socials span{width:20px;height:20px;border-radius:50%;background:var(--white)}
.copy{position:absolute;top:250px;left:0;width:1200px;text-align:center;font-size:9px;color:#d0d0d8}
</style>
</head>
<body>

<header class="hero">
  <div class="hero-photo" role="img" aria-label="Smiling woman in a light blue shirt seated beside an IV drip stand in a bright clinic room"></div>
  <div class="brand">VELQO</div>
  <nav class="nav">
    <a class="active" href="#">Home</a><a href="#">About us</a><a href="#">Services</a><a href="#">IV Nutritional Therapy</a><a href="#">Blog</a><a href="#">Contact us</a><a class="book" href="#">Book now</a>
  </nav>
  <h1>Revitalize with<br><span class="accent">IV Nutrition</span></h1>
  <p>Boost energy, immunity, and hydration with our expert IV therapy treatments!</p>
  <a class="btn" href="#">Book an appointment</a>
</header>

<section class="benefits">
  <div class="photo" role="img" aria-label="IV bag filled with fresh fruit slices submerged in water"></div>
  <h2>IV Therapy’s<br>Health Benefits</h2>
  <div class="rule"></div>
  <p class="intro">Lorem ipsum dolor sit amet, consectetur adipiscing elit, sed do eiusmod tempor incididunt ut labore et dolore magna aliqua. Ut enim ad minim veniam, quis nostrud exercitation ullamco laboris nisi ut aliquip ex ea commodo consequat. Duis aute irure dolor in reprehenderit.</p>
  <div class="benefit" style="top:284px"><div class="ico"><svg width="20" height="20" viewBox="0 0 20 20"><path d="M10 17 3 10a4 4 0 0 1 7-5 4 4 0 0 1 7 5z" fill="#fff"/></svg></div><div><h4>Gut Health IV</h4><p>Lorem ipsum dolor sit amet, consectetur adipiscing elit, sed do eiusmod tempor incididunt ut labore</p></div></div>
  <div class="benefit" style="top:352px"><div class="ico"><svg width="20" height="20" viewBox="0 0 20 20"><circle cx="10" cy="9" r="6" fill="none" stroke="#fff" stroke-width="2"/><path d="M7 16h6" stroke="#fff" stroke-width="2"/></svg></div><div><h4>Stress IV</h4><p>Lorem ipsum dolor sit amet, consectetur adipiscing elit, sed do eiusmod tempor incididunt ut labore</p></div></div>
  <div class="benefit" style="top:423px"><div class="ico"><svg width="20" height="20" viewBox="0 0 20 20"><path d="M4 15c2-6 4-9 7-9l2 3c-2 0-3 2-3 4h5v2z" fill="#fff"/></svg></div><div><h4>Muscle IV</h4><p>Lorem ipsum dolor sit amet, consectetur adipiscing elit, sed do eiusmod tempor incididunt ut labore</p></div></div>
  <div class="benefit" style="top:494px"><div class="ico"><svg width="20" height="20" viewBox="0 0 20 20"><rect x="6" y="3" width="8" height="11" rx="2" fill="none" stroke="#fff" stroke-width="2"/><path d="M10 14v4" stroke="#fff" stroke-width="2"/></svg></div><div><h4>Longevity IV</h4><p>Lorem ipsum dolor sit amet, consectetur adipiscing elit, sed do eiusmod tempor incididunt ut labore</p></div></div>
</section>

<section class="featured">
  <h2>Featured IV Therapies</h2>
  <div class="rule"></div>

  <div class="therapy-text" style="left:161px;top:232px"><h3>Immune Support<br>IV Therapy</h3><p>Lorem ipsum dolor sit amet, consectetur adipiscing elit, sed do eiusmod tempor incididunt ut labore et dolore magna aliqua. Ut enim ad minim veniam, quis nostrud exercitation ullamco laboris nisi ut aliquip ex ea commodo consequat. Duis aute irure dolor in reprehenderit.</p><a class="btn" href="#">Book an appointment</a></div>
  <div class="therapy-photo" style="left:482px;top:179px;background:linear-gradient(110deg,#d7d2cc 0%,#6a4a5c 40%,#3b2437 70%,#e9e4de 100%)" role="img" aria-label="Man resting while receiving a fruit-filled IV drip"></div>

  <div class="therapy-photo" style="left:161px;top:593px;background:linear-gradient(180deg,#6aa6e6 0%,#5f9fe3 100%)" role="img" aria-label="Clear saline IV bag on a blue background"></div>
  <div class="therapy-text" style="left:765px;top:642px"><h3>Celebration<br>IV Therapy</h3><p>Lorem ipsum dolor sit amet, consectetur adipiscing elit, sed do eiusmod tempor incididunt ut labore et dolore magna aliqua. Ut enim ad minim veniam, quis nostrud exercitation ullamco laboris nisi ut aliquip ex ea commodo consequat. Duis aute irure dolor in reprehenderit.</p><a class="btn" href="#">Book an appointment</a></div>

  <div class="therapy-text" style="left:161px;top:1040px"><h3>High-Dose<br>Vitamin C<br>IV Therapy</h3><p>Lorem ipsum dolor sit amet, consectetur adipiscing elit, sed do eiusmod tempor incididunt ut labore et dolore magna aliqua. Ut enim ad minim veniam, quis nostrud exercitation ullamco laboris nisi ut aliquip ex ea commodo consequat. Duis aute irure dolor in reprehenderit.</p><a class="btn" href="#">Book an appointment</a></div>
  <div class="therapy-photo" style="left:482px;top:1007px;background:linear-gradient(160deg,#d9d9d5 0%,#c9c9c3 40%,#e7b96a 60%,#cfcfca 100%)" role="img" aria-label="Hand holding an IV bag filled with citrus slices"></div>
</section>

<section class="testimonials">
  <h2>Testimonials</h2>
  <div class="rule"></div>
  <div class="t-card">
    <div class="t-photo" role="img" aria-label="Woman raising her arms in a field at sunset"></div>
    <div class="t-body">
      <div class="t-mark">“</div>
      <p>Lorem ipsum dolor sit amet, consectetur adipiscing elit, sed do eiusmod tempor incididunt ut labore et dolore magna aliqua. Ut enim ad minim veniam, quis nostrud exercitation ullamco laboris nisi ut aliquip ex ea com modo consequat. Duis aute irure dolor in reprehenderit. because those who do not know how to pursue pleasure rationally encounter consequences that are extremely painful.</p>
      <div class="t-rule"></div>
      <div class="t-name">DARA WENLOW</div>
    </div>
  </div>
  <div class="dots"><span class="on"></span><span></span><span></span><span></span></div>
</section>

<section class="live">
  <div class="drip" role="img" aria-label="IV drip bag with tubing hanging from the top edge"></div>
  <h2>Live Your Best Life with IV Therapy</h2>
  <div class="rule"></div>
  <div class="live-card" style="left:163px">
    <svg width="54" height="54" viewBox="0 0 54 54" fill="none" stroke="#6b9b2e" stroke-width="2"><path d="M27 5 45 12v14c0 12-8 20-18 24C17 46 9 38 9 26V12z"/><circle cx="27" cy="27" r="7"/><path d="M27 17v4M27 33v4M17 27h4M33 27h4"/></svg>
    <h3>Immune Health</h3>
    <p>Lorem ipsum dolor sit amet, consectetur adipiscing elit, sed do eiusmod tempor incididunt ut labore et dolore magna aliqua. Ut enim ad minim veniam, quis nostrud exercitation.</p>
  </div>
  <div class="live-card" style="left:461px">
    <svg width="76" height="54" viewBox="0 0 76 54" fill="none" stroke="#6b9b2e" stroke-width="2"><path d="M12 22l8-5 8 5v9l-8 5-8-5z"/><path d="M28 22l8-5 8 5v9l-8 5-8-5z"/><path d="M20 36l8-5 8 5v9l-8 5-8-5z"/><path d="M44 22l8-5 8 5v9l-8 5-8-5z"/></svg>
    <h3>Restore Hormones</h3>
    <p>Lorem ipsum dolor sit amet, consectetur adipiscing elit, sed do eiusmod tempor incididunt ut labore et dolore magna aliqua. Ut enim ad minim veniam, quis nostrud exercitation.</p>
  </div>
  <div class="live-card" style="left:760px">
    <svg width="54" height="54" viewBox="0 0 54 54" fill="none" stroke="#6b9b2e" stroke-width="2"><circle cx="27" cy="27" r="22"/><circle cx="27" cy="27" r="16"/><path d="M30 15 21 29h7l-3 11 9-15h-7z"/></svg>
    <h3>Boost Energy</h3>
    <p>Lorem ipsum dolor sit amet, consectetur adipiscing elit, sed do eiusmod tempor incididunt ut labore et dolore magna aliqua. Ut enim ad minim veniam, quis nostrud exercitation.</p>
  </div>
</section>

<section class="treat">
  <h2>Treatments<br>Personalized<br>to You</h2>
  <div class="rule"></div>
  <p>Sed ut perspiciatis unde omnis iste natus error sit voluptatem accusantium doloremque laudantium, totam rem aperiam, eaque ipsa quae ab illo inventore veritatis et quasi architecto beatae vitae dicta sunt explicabo. Nemo enim ipsam voluptatem quia voluptas sit aspernatur.</p>
  <a class="btn" href="#">Read more</a>
  <div class="photo" role="img" aria-label="Smiling woman in bed receiving IV therapy while a clinician takes notes"></div>
</section>

<section class="schedule" aria-label="Schedule a consultation">
  <h2>Schedule a Consultation</h2>
  <p class="sub">Your health is important, and we welcome the opportunity to help you heal.</p>
  <p class="body">Lorem ipsum dolor sit amet, consectetur adipiscing elit, sed do eiusmod tempor incididunt ut labore et dolore magna aliqua. Ut enim ad minim veniam, quis nostrud</p>
  <a class="btn" href="#">Book an appointment</a>
</section>

<footer class="site-footer">
  <div class="brand">VELQO</div>
  <div class="f-col" style="left:446px">
    <h4>CONTACT US</h4>
    <ul>
      <li><svg width="12" height="12" viewBox="0 0 12 12"><path d="M6 11S2 7 2 4.5a4 4 0 0 1 8 0C10 7 6 11 6 11z" fill="#fff"/><circle cx="6" cy="4.5" r="1.4" fill="#000"/></svg><span>482 Meadowlark Ave. Suite 2-110<br>Brinford, TN 37190</span></li>
      <li><svg width="12" height="12" viewBox="0 0 12 12"><path d="M2 1h3l1 3-2 1a6 6 0 0 0 3 3l1-2 3 1v3c-6 0-10-4-10-9z" fill="#fff"/></svg><span>+1 555 014 2290</span></li>
      <li><svg width="12" height="12" viewBox="0 0 12 12"><rect x="1" y="2.5" width="10" height="7" fill="#fff"/><path d="M1 3l5 4 5-4" stroke="#000" fill="none"/></svg><span>info@velqo.com</span></li>
    </ul>
  </div>
  <div class="f-col f-menu" style="left:718px">
    <h4>MENU</h4>
    <ul><li>HOME</li><li>ABOUT US</li><li>SERVICES</li><li>IV Nutritional Therapy</li><li>BLOG</li><li>CONTACT US</li></ul>
  </div>
  <div class="f-col" style="left:913px">
    <h4>FOLLOW US</h4>
    <div class="socials" aria-label="Social media links"><span></span><span></span><span></span><span></span><span></span></div>
  </div>
  <p class="copy">Copyright © 2025 All Rights Reserved</p>
</footer>

</body>
</html>
```